Alberta, Canada based Environmental Oilfield Consultant need a Business Card Design

We need a business card design for a year old company based in Edmonton, Alberta, Canada called Cindermoor Consulting Inc. We are environmental consultants primarily for oilfield based companies (pipeline cleanup, site consultations, environmental site training, and site evaluations).

We like the color blue or green, something very clean and crisp looking.
We don't really care if there is an otter on it but most of our work is land based and nothing really to do with oceans or larger bodies of water.

The name Cindermoor was the name of our fathers boat, and named our company that in his memory.

```html
<!DOCTYPE html>
<html lang="en">
<head>
<meta charset="utf-8">
<title>Cindermoor Consulting Inc. — Business Card</title>
<link rel="stylesheet" href="https://fonts.googleapis.com/css2?family=Exo+2:wght@400;600;800&display=swap">
<style>
  :root {
    --backdrop: #e4e5e7;
    --card-white: #ffffff;
    --card-black: #1b1b1b;
    --ink: #2a2a2a;
    --ink-soft: #555555;
    --amber: #f7b718;
    --amber-deep: #f28c1e;
    --steel: #8a8a8a;
    --steel-light: #cfcfcf;
  }
  * { margin: 0; padding: 0; box-sizing: border-box; }
  html, body { width: 1200px; height: 853px; overflow: hidden; }
  body {
    background: var(--backdrop);
    font-family: "Exo 2", Arial, sans-serif;
    display: flex;
    align-items: center;
    justify-content: center;
    gap: 80px;
  }
  .card {
    position: relative;
    width: 400px;
    height: 700px;
    overflow: hidden;
    box-shadow: 0 6px 18px rgba(0,0,0,0.18);
  }
  .card-back { background: var(--card-black); }
  .card-front { background: var(--card-white); }
  .swoosh { position: absolute; inset: 0; width: 100%; height: 100%; }

  .brand {
    position: absolute;
    font-weight: 800;
    line-height: 0.95;
    letter-spacing: 0.5px;
  }
  .card-front .brand { top: 48px; right: 34px; text-align: right; color: var(--ink); font-size: 46px; }
  .card-back .brand { top: 268px; left: 0; right: 0; text-align: center; color: var(--card-white); font-size: 52px; }

  .contact {
    position: absolute;
    left: 36px;
    right: 36px;
    top: 330px;
    color: var(--ink);
  }
  .person-name { font-size: 32px; font-weight: 600; letter-spacing: 2px; }
  .person-role { font-size: 13px; color: var(--amber-deep); letter-spacing: 1.5px; margin-top: 2px; }
  .rule { height: 3px; margin: 12px 0 16px; background: linear-gradient(90deg, var(--amber-deep), var(--amber)); }
  .details { display: flex; justify-content: space-between; font-size: 13px; color: var(--ink-soft); }
  .details ul { list-style: none; }
  .details li { display: flex; align-items: center; gap: 7px; margin-bottom: 8px; }
  .dot {
    width: 14px; height: 14px; border-radius: 50%;
    background: var(--amber);
    display: inline-flex; align-items: center; justify-content: center;
  }
  .dot svg { width: 9px; height: 9px; }

  .address-band {
    position: absolute;
    left: 0; right: 0; bottom: 0;
    height: 170px;
    background: radial-gradient(ellipse at 40% 55%, #ffd21e 0%, var(--amber) 45%, var(--amber-deep) 100%);
    display: flex;
    flex-direction: column;
    justify-content: center;
    padding: 0 36px;
    color: var(--ink);
    font-size: 22px;
    font-weight: 600;
    letter-spacing: 1px;
    line-height: 1.35;
  }
</style>
</head>
<body>

  <section class="card card-back" aria-label="Card back">
    <svg class="swoosh" viewBox="0 0 400 700" preserveAspectRatio="none" aria-hidden="true">
      <path d="M400 40 C250 160 120 330 0 620 L0 660 C140 360 260 190 400 70 Z" fill="var(--amber)"/>
      <path d="M0 540 C90 350 220 170 400 20 L400 0 C210 150 80 320 0 500 Z" fill="var(--steel)"/>
      <path d="M400 470 C300 560 200 640 140 700 L170 700 C230 645 320 570 400 510 Z" fill="var(--amber)"/>
    </svg>
    <div class="brand">Cindermoor<br>Consulting</div>
  </section>

  <section class="card card-front" aria-label="Card front">
    <svg class="swoosh" viewBox="0 0 400 700" preserveAspectRatio="none" aria-hidden="true">
      <path d="M400 190 C260 200 90 240 0 300 L0 308 C100 252 260 214 400 206 Z" fill="var(--steel)"/>
      <path d="M400 0 L400 20 C300 60 130 150 0 250 L0 232 C130 130 290 40 360 0 Z" fill="var(--amber)"/>
      <path d="M340 0 C280 30 200 70 150 100 C210 60 270 25 310 0 Z" fill="var(--amber-deep)"/>
    </svg>
    <div class="brand">Cindermoor<br>Consulting</div>

    <div class="contact">
      <h1 class="person-name">EVAN MARLOW</h1>
      <p class="person-role">GENERAL MANAGER</p>
      <div class="rule"></div>
      <div class="details">
        <ul>
          <li><span class="dot"><svg viewBox="0 0 10 10"><path d="M2 1 L4 1 L4.6 3 L3.6 3.8 C4 5 5 6 6.2 6.4 L7 5.4 L9 6 L9 8 C5 8.5 1.5 5 2 1 Z" fill="#fff"/></svg></span>780 555 0142</li>
          <li><span class="dot"><svg viewBox="0 0 10 10"><path d="M2 1 L4 1 L4.6 3 L3.6 3.8 C4 5 5 6 6.2 6.4 L7 5.4 L9 6 L9 8 C5 8.5 1.5 5 2 1 Z" fill="#fff"/></svg></span>780 555 0143</li>
        </ul>
        <ul>
          <li><span class="dot"><svg viewBox="0 0 10 10"><rect x="1" y="2.5" width="8" height="5" fill="#fff"/><path d="M1 2.5 L5 5.5 L9 2.5" stroke="#f7b718" fill="none"/></svg></span>evan@cindermoor.ca</li>
          <li><span class="dot"><svg viewBox="0 0 10 10"><circle cx="5" cy="5" r="3.5" stroke="#fff" fill="none"/><path d="M1.5 5 H8.5 M5 1.5 V8.5" stroke="#fff"/></svg></span>www.cindermoor.ca</li>
        </ul>
      </div>
    </div>

    <div class="address-band">
      <p>42 Birchline Road,</p>
      <p>Unit 3 North</p>
    </div>
  </section>

</body>
</html>
```